BrindleStaffing Business Card Design

We are a staffing company finding positions for dedicated nurses and physicians.

Target Market(s)

Business Professionals

Industry/Entity Type

Staffing

Contact Information for Business Card

Gordon Pratley
Chairman
417 39th Avenue South
SAINT PETERSBURG FL 33712
813-555-4172 Mobile
813-555-8036 Fax
gpratley@brindlestaffing.com
www.brindlestaffing.com

Font styles to use
Sans Serif

Colors
fbee3e
f04a50
f37122

Requirements
Must have
• Logo Attached, see colors below. We'd like to see Yellow, Orange and Red.

```html
<!DOCTYPE html>
<html lang="en">
<head>
<meta charset="utf-8">
<title>BrindleStaffing Business Card</title>
<link rel="stylesheet" href="https://fonts.googleapis.com/css2?family=Poppins:wght@600&family=Source+Sans+3:wght@400;700&display=swap">
<style>
  :root {
    --ink: #000000;
    --brand-yellow: #fbee3e;
    --brand-orange: #f37122;
    --brand-red: #f04a50;
    --paper: #ffffff;
    --stage-light: #b6b7ba;
    --stage-dark: #7d7e82;
  }
  * { margin: 0; padding: 0; box-sizing: border-box; }
  html, body { width: 1200px; height: 1180px; overflow: hidden; }
  body {
    position: relative;
    background: radial-gradient(circle at 50% 48%, var(--stage-light) 0%, var(--stage-dark) 85%);
    font-family: "Source Sans 3", sans-serif;
    color: var(--paper);
  }
  .card {
    position: absolute;
    width: 716px;
    height: 408px;
    border-radius: 39px;
    background: var(--ink);
    overflow: hidden;
  }
  .card--front { left: 387px; top: 120px; }
  .card--back { left: 108px; top: 611px; }

  .brand-name {
    position: absolute;
    left: 0; right: 0;
    text-align: center;
    font-family: "Poppins", sans-serif;
    font-weight: 600;
    font-size: 56px;
    line-height: 1;
    letter-spacing: -1.5px;
    color: var(--brand-yellow);
  }
  .card--front .brand-name { top: 78px; }
  .card--back .brand-name { top: 150px; }

  .band-top {
    position: absolute;
    left: 0; top: 210px;
    width: 100%; height: 40px;
    background: var(--brand-orange);
  }
  .band-bottom {
    position: absolute;
    left: 0; top: 250px;
    width: 100%; height: 158px;
    background: var(--brand-red);
  }
  .name-plate {
    position: absolute;
    left: 0; top: 210px;
    width: 368px; height: 85px;
    background: var(--brand-orange);
    border-bottom: 3px solid var(--paper);
  }
  .person-name {
    position: absolute;
    left: 0; width: 310px;
    top: 218px;
    text-align: center;
    font-weight: 700;
    font-size: 31px;
    line-height: 1.1;
  }
  .person-title {
    position: absolute;
    left: 0; width: 310px;
    top: 255px;
    text-align: center;
    font-size: 25px;
    line-height: 1.1;
  }
  .portrait {
    position: absolute;
    left: 315px; top: 198px;
    width: 98px; height: 98px;
    border-radius: 50%;
    background: var(--brand-orange);
    border: 3px solid var(--paper);
  }
  .address {
    position: absolute;
    left: 33px; top: 328px;
    font-size: 18px;
    line-height: 28px;
  }
  .address-line { display: flex; align-items: center; }
  .address-line--indent { padding-left: 18px; }
  .contact-list {
    position: absolute;
    left: 401px; top: 300px;
    list-style: none;
    font-size: 18px;
    line-height: 24px;
  }
  .contact-list li { display: flex; align-items: center; }
  .icon { width: 15px; height: 15px; margin-right: 4px; flex: none; }
  .contact-list .icon { margin-right: 11px; }

  .web-address {
    position: absolute;
    left: 0; right: 0; top: 264px;
    text-align: center;
    font-size: 22px;
    letter-spacing: 3px;
    color: var(--paper);
  }
  .web-address .domain { font-weight: 700; color: var(--brand-orange); }
</style>
</head>
<body>
  <section class="card card--front">
    <div class="brand-name">BrindleStaffing</div>
    <div class="band-top"></div>
    <div class="band-bottom"></div>
    <div class="name-plate"></div>
    <div class="person-name">Gordon Pratley</div>
    <div class="person-title">Chairman</div>
    <div class="portrait" role="img" aria-label="Portrait photo placeholder"></div>

    <div class="address">
      <div class="address-line">
        <svg class="icon" viewBox="0 0 16 16" aria-hidden="true"><circle cx="8" cy="8" r="7" fill="none" stroke="#fff" stroke-width="1.4"/><path d="M8 3.5a3 3 0 0 0-3 3c0 2.2 3 5.5 3 5.5s3-3.3 3-5.5a3 3 0 0 0-3-3z" fill="none" stroke="#fff" stroke-width="1.3"/><circle cx="8" cy="6.5" r="1" fill="#fff"/></svg>
        417 39th avenue south
      </div>
      <div class="address-line address-line--indent">Saint petersburg fl 33712</div>
    </div>

    <ul class="contact-list">
      <li>
        <svg class="icon" viewBox="0 0 16 16" aria-hidden="true"><circle cx="8" cy="8" r="7" fill="none" stroke="#fff" stroke-width="1.4"/><path d="M6 4.2l1.3 2-1 1a5 5 0 0 0 2.5 2.5l1-1 2 1.3-.8 1.3c-3 .2-5.8-2.6-5.6-5.6z" fill="#fff"/></svg>
        813-555-4172 Mobile
      </li>
      <li>
        <svg class="icon" viewBox="0 0 16 16" aria-hidden="true"><rect x="4" y="1.5" width="8" height="4" fill="none" stroke="#fff" stroke-width="1.2"/><rect x="1.5" y="5.5" width="13" height="6" rx="1" fill="#fff"/><rect x="4" y="10" width="8" height="4.5" fill="#fff" stroke="#f04a50" stroke-width="1"/></svg>
        813-555-8036 Fax
      </li>
      <li>
        <svg class="icon" viewBox="0 0 16 16" aria-hidden="true"><path d="M1.5 6.5L8 2l6.5 4.5V14h-13z" fill="#fff"/><path d="M1.5 6.5L8 10.5l6.5-4" fill="none" stroke="#f04a50" stroke-width="1.2"/></svg>
        gpratley@brindlestaffing.com
      </li>
      <li>
        <svg class="icon" viewBox="0 0 16 16" aria-hidden="true" fill="none" stroke="#fff" stroke-width="1.1"><circle cx="8" cy="8" r="7"/><ellipse cx="8" cy="8" rx="3" ry="7"/><path d="M1 8h14M2 4.5h12M2 11.5h12"/></svg>
        www.brindlestaffing.com
      </li>
    </ul>
  </section>

  <section class="card card--back">
    <div class="brand-name">BrindleStaffing</div>
    <div class="web-address">www.<span class="domain">brindlestaffing</span>.com</div>
  </section>
</body>
</html>
```